Bry7Legal Letterhead

Need a new letterhead for my law firm.
IDENTIFYING INFORMATION BELOW:
Anselmo R Quintara III
Attorney at Law
Address: 2847 Larkspur Blvd, Ste 300, Dallas, TX 75204
Phone: 877-482-6017
Fax: 469-738-1452
Email: bry@bry7legal.example
Website: www.bry7legal.example

Colors
0054AA
0677BA
7BADD7
CADEEF
E8F1F8

Requirements
Must have
• Logo needs to be on the letterhead, along with identifying information which is included in the project description.

```html
<!DOCTYPE html>
<html lang="en">
<head>
<meta charset="utf-8">
<title>Bry7Legal Letterhead</title>
<link href="https://fonts.googleapis.com/css2?family=Montserrat:wght@400;500;800&family=Arimo&display=swap" rel="stylesheet">
<style>
  :root {
    --backdrop: #ececec;
    --paper: #ffffff;
    --ink: #000000;
    --brand-blue: #0677ba;
    --accent-blue: #1a9ad6;
    --deep-blue: #0054aa;
    --text-dark: #3a3a3a;
    --text-muted: #8a8a8a;
    --signature-tone: #d9d9d9;
  }
  * { margin: 0; padding: 0; box-sizing: border-box; }
  html, body { width: 1200px; height: 1200px; overflow: hidden; background: var(--backdrop); }
  .letterhead {
    position: absolute; left: 204px; top: 40px;
    width: 792px; height: 1120px;
    background: var(--paper);
    font-family: "Montserrat", sans-serif;
    box-shadow: 0 2px 10px rgba(0,0,0,.12);
  }
  .brand-name {
    position: absolute; top: 44px; left: 0; width: 100%;
    text-align: center; font-weight: 800; font-size: 38px; line-height: 1;
    letter-spacing: 1px; color: var(--ink);
  }
  .header-band { position: absolute; left: 0; width: 100%; }
  .header-band--black { top: 85px; height: 12px; background: var(--ink); }
  .header-band--blue { top: 101px; height: 2.5px; background: linear-gradient(90deg, var(--deep-blue), var(--accent-blue)); }

  .recipient { position: absolute; left: 81px; top: 250px; }
  .recipient__label { font-size: 14px; letter-spacing: 2px; color: var(--text-dark); }
  .recipient__name { margin-top: 6px; font-size: 14px; color: var(--accent-blue); }
  .recipient__line { font-size: 11px; line-height: 17.5px; color: var(--text-muted); }
  .recipient__name + .recipient__line { margin-top: 6px; }
  .letter-date { position: absolute; right: 80px; top: 250px; font-size: 11.5px; color: var(--text-dark); }

  .letter-body {
    position: absolute; left: 81px; top: 400px; width: 632px;
    font-size: 11.6px; line-height: 14.2px; color: var(--text-muted);
    text-align: justify;
  }
  .letter-body p { margin-bottom: 13.8px; }

  .signature-mark { position: absolute; left: 81px; top: 794px; width: 136px; height: 28px; }
  .signer { position: absolute; left: 79px; top: 834px; }
  .signer__name { font-size: 13px; color: var(--text-dark); }
  .signer__title { font-size: 10.5px; color: var(--text-muted); margin-top: 2px; }

  .footer { position: absolute; left: 0; width: 100%; top: 1050px; font-family: "Arimo", sans-serif; font-size: 13px; color: var(--text-dark); }
  .footer__address { display: flex; align-items: center; justify-content: center; gap: 5px; }
  .footer__rule { width: 85px; height: 1px; background: var(--text-dark); }
  .footer__contacts { display: flex; justify-content: center; gap: 9px; margin-top: 6px; }
  .contact-item { display: flex; align-items: center; gap: 5px; }
  .contact-item svg { width: 11px; height: 11px; fill: var(--brand-blue); }
</style>
</head>
<body>
<main class="letterhead">
  <div class="brand-name">BRY7LEGAL</div>
  <div class="header-band header-band--black"></div>
  <div class="header-band header-band--blue"></div>

  <section class="recipient">
    <div class="recipient__label">TO</div>
    <div class="recipient__name">Daniel Ferreira</div>
    <div class="recipient__line">Human Resources</div>
    <div class="recipient__line">Northwind Systems Inc.</div>
    <div class="recipient__line">2210-B Hollis Street, Westbrook</div>
    <div class="recipient__line">E42 USA</div>
  </section>
  <div class="letter-date">Friday, 01/01/2018</div>

  <section class="letter-body">
    <p>Lorem ipsum dolor sit amet, consectetuer adipiscing elit, sed diam nonmmy nibh euismod tincidunt ut laoreet dolore magna aliquam erat volutpat. Ut wisi enim ad minim veniam, quis nostrud exerci tationmcorper suscipit lobortis nisl ut aliquip ex ea commodo consequat. Duis autem vel eum iriure dolor in hendrerit in vulputate velit esse molestie consequat, vel illum dolore eu feugiat nulla facilisis at vero eros et accumsan et iusto odio dignissim qui blandit praesent luptatum zzril delenit augue duis dolore te feugait nulla facilisi.</p>
    <p>Nam liber tempor cum soluta nobis eleifend option congue nihil imprdiet doming id quod mazim placerat facer possim assum. Typi non habent claritatem insitam;</p>
    <p>Est usus legentis in iis qui facit eorum claritatem.</p>
    <p>Investigationes demonstraverunt lectores legere me lius quod ii legunt saepius. Claritas est etiam processus dynamicus, qui sequitur mutationem consuetudium lectorum. Mirum est notare quam littera gothica, quam nunc putamus parum claram, anteposuerit litterarum formas humanitatis per seacula quarta decima et quinta decima. Eodem modo typi, qui nunc nobis videntur parum clari, fiant sollemnes in futurum.</p>
    <p>consectetuer adipiscing elit, sed diam nonummy nibh euismod tincidunt ut laoreet dolore magna aliquam erat volutpat. Ut wisi enim ad minim veniam, quis nostrud exerci tation ullamcorper suscipit lobortis nisl ut aliquip ex ea commodo consequat. Duis autem vel eum iriure dolor in hendrerit in vulputate velit esse molestie consequat, vel illum dolore eu feugiat nulla facilisis at vero eros et accumsan et iusto odio dignissim qui blandit praesent luptatum zzril delenit augue duis dolore te feugait nulla facilisi.</p>
    <p>Nam liber tempor cum soluta nobis eleifend option congue nihil imperdiet .</p>
  </section>

  <svg class="signature-mark" role="img" aria-label="Handwritten signature of the signer" viewBox="0 0 136 28">
    <rect width="136" height="28" rx="3" fill="var(--signature-tone)"/>
  </svg>
  <div class="signer">
    <div class="signer__name">Anselmo R Quintara III</div>
    <div class="signer__title">Managing Director</div>
  </div>

  <footer class="footer">
    <div class="footer__address">
      <span class="footer__rule"></span>
      <span>2847 Larkspur Blvd, Ste 300, Dallas, TX 75204</span>
      <span class="footer__rule"></span>
    </div>
    <div class="footer__contacts">
      <span class="contact-item">
        <svg viewBox="0 0 12 12"><path d="M2.4 0.6l1.8 0 .8 2.6-1.2 1a7 7 0 0 0 3 3l1-1.2 2.6.8 0 1.8c0 .9-.7 1.4-1.6 1.3C4.8 9.5 1.9 6.6 1.2 2.2 1 1.3 1.5.6 2.4.6z"/></svg>
        877-482-6017
      </span>
      <span class="contact-item">
        <svg viewBox="0 0 12 12"><rect x="3" y="0.5" width="6" height="3.5"/><rect x="0.5" y="4.5" width="11" height="5" rx="1"/><rect x="3" y="8" width="6" height="3.5" fill="#fff" stroke="var(--brand-blue)"/></svg>
        469-738-1452
      </span>
      <span class="contact-item">
        <svg viewBox="0 0 12 12"><rect x="0.5" y="2" width="11" height="8"/><path d="M0.5 2l5.5 4.5L11.5 2" fill="none" stroke="#fff" stroke-width="1"/></svg>
        bry@bry7legal.example
      </span>
      <span class="contact-item">
        <svg viewBox="0 0 12 12"><circle cx="6" cy="6" r="5.5"/><path d="M3 4c1 0 2 1 1.5 2S5 8 6 9M8 2.5c-.5 1 .5 2 1.5 2" fill="none" stroke="#fff" stroke-width="1"/></svg>
        www.bry7legal.example
      </span>
    </div>
  </footer>
</main>
</body>
</html>
```